Stationery Design Project

Hi All,

We need you to design stationary for a new Business and Accounting Advisory Firm. We have already got the logo designed and it is attached. If you could also if possible, match the fonts in your design to that on the logo’s provided.

What we need:
- Business Card
- A4 Letter head
- A4 Folders
- PPT template (Title page and regular page)

And what ever else you want to throw in.

We are in the process of getting the web site designed, however below is a list of websites which we like which will give you an understanding of the style that we are going for.

- plivant.example
- moldrabay.example
- tarvenhook.example
- quillorbank.example

I look forward to your seeing your design.
Updates

Hi All,

I have just realised that I forgot that i need to include a Sworn Ledgerkeepers image on the letter head, please find attaced as File 1. Could you please have this image in the bottom left header.

Regards,

Marcus

Industry/Entity Type

Business

Requirements
Must have
• Outputs:
- Documents ready to print
- Generic editable information
- Pdf copies of the documents
- Word version of letterhead

```html
<!DOCTYPE html>
<html lang="en">
<head>
<meta charset="utf-8">
<title>Brennick Partners – Business Card</title>
<link rel="stylesheet" href="https://fonts.googleapis.com/css2?family=EB+Garamond:wght@400&family=Arimo:wght@400&display=swap">
<style>
  :root {
    --backdrop: #e4e4e4;
    --card-dark: #3d3d3d;
    --card-light: #ffffff;
    --brand-orange: #f7941d;
    --brand-teal: #3fb6d3;
    --brand-blue: #3a5fa0;
    --ink-grey: #555555;
    --name-light: #ececec;
    --card-edge: #d6d6d6;
  }
  * { box-sizing: border-box; margin: 0; padding: 0; }
  html, body {
    width: 1200px;
    height: 1000px;
    overflow: hidden;
    background: var(--backdrop);
  }
  .canvas {
    position: relative;
    width: 1200px;
    height: 1000px;
  }
  .card {
    position: absolute;
    overflow: hidden;
  }
  .card--front {
    left: 277px;
    top: 136px;
    width: 647px;
    height: 324px;
    background: var(--card-dark);
  }
  .card--back {
    left: 276px;
    top: 531px;
    width: 645px;
    height: 321px;
    background: var(--card-light);
    border: 1px solid var(--card-edge);
    font-family: "Arimo", Arial, sans-serif;
    font-size: 19px;
    color: var(--ink-grey);
  }
  .brand {
    position: absolute;
    left: 108px;
    top: 118px;
    display: flex;
    align-items: center;
    gap: 20px;
  }
  .brand__dot {
    width: 46px;
    height: 46px;
    border-radius: 50%;
    background: var(--brand-orange);
  }
  .brand__name {
    font-family: "EB Garamond", Georgia, serif;
    font-weight: 400;
    font-size: 42px;
    color: var(--name-light);
    letter-spacing: 0.2px;
  }
  .web {
    position: absolute;
    left: 45px;
    top: 35px;
    color: var(--brand-orange);
  }
  .address {
    position: absolute;
    left: 374px;
    top: 35px;
    font-style: normal;
    line-height: 25px;
  }
  .contacts {
    position: absolute;
    left: 341px;
    top: 177px;
    list-style: none;
    line-height: 27.5px;
  }
  .contacts__label {
    display: inline-block;
    width: 33px;
    color: var(--brand-orange);
  }
  .accent {
    position: absolute;
    left: -2px;
    bottom: -2px;
  }
</style>
</head>
<body>
<main class="canvas">
  <section class="card card--front" aria-label="Business card front">
    <div class="brand">
      <span class="brand__dot" aria-hidden="true"></span>
      <span class="brand__name">Brennick Partners</span>
    </div>
  </section>

  <section class="card card--back" aria-label="Business card back">
    <p class="web">www.xxxxxxx.com.au</p>
    <address class="address">14 Lorem Street, Aenean<br>Anriean VIC 3000</address>
    <ul class="contacts">
      <li><span class="contacts__label">t</span>03 000 000</li>
      <li><span class="contacts__label">f</span>03 000 000</li>
      <li><span class="contacts__label">m</span>0400 000 000</li>
      <li><span class="contacts__label">e</span>xxxxx@xxxxxx.com.au</li>
    </ul>
    <svg class="accent" width="310" height="180" viewBox="0 0 310 180" aria-hidden="true">
      <circle cx="90" cy="200" r="150" fill="var(--brand-teal)"/>
    </svg>
  </section>
</main>
</body>
</html>
```